Computer Consulting Brochure

Computer Consulting services for schools, small businesses, local governments and medical offices. We design networks, security, monitoring, applications for these environments.
Updates
Project Deadline Extended Reason: I provided a condensed document so as not to overwhelm designers. This document covers only pertinent info that can be further condensed if necessary for physical size constraints. Added Friday, April 7, 2017
Target Market(s)
Schools, Small Businesses, Medical Offices, Local Governments. 4 brochures that are identical except for a section that specifically describes the 4 markets.
Industry/Entity Type
Computer
Colors
Designer to choose colors to be used in the design.
Look and feel
Each slider illustrates characteristics of the customer's brand and the style your logo design should communicate.

```html
<!DOCTYPE html>
<html lang="en">
<head>
<meta charset="utf-8">
<title>NorthLoop IT Brochure</title>
<link rel="stylesheet" href="https://fonts.googleapis.com/css2?family=Oswald:wght@400;500&family=Roboto+Condensed:wght@300;400;700&display=swap">
<style>
:root{
  --page:#ececec;
  --teal:#1f9fc4;
  --teal-light:#6cc6de;
  --gold:#f7b500;
  --gold-deep:#f29b12;
  --gold-pale:#fdf3cf;
  --ink:#3c3c3c;
  --white:#ffffff;
}
*{box-sizing:border-box;margin:0;padding:0}
html,body{width:1200px;height:1200px;overflow:hidden;background:var(--page)}
body{font-family:"Roboto Condensed",sans-serif;color:var(--ink);position:relative}
.spread{position:absolute;left:220px;width:760px;height:585px;display:flex;background:var(--white);box-shadow:0 2px 8px rgba(0,0,0,.18);overflow:hidden}
.spread--outside{top:12px}
.spread--inside{top:603px}
.panel{width:253.33px;height:100%;position:relative;overflow:hidden;flex:none}
.heading{font-family:"Oswald",sans-serif;font-weight:500;color:var(--teal);font-size:18px;letter-spacing:.2px;line-height:1.1}
.lead{color:var(--teal);font-weight:700;font-size:10px;line-height:1.25;margin:5px 0 8px}
.bullets{list-style:none}
.bullets li{font-size:8.8px;line-height:1.33;padding-left:10px;position:relative;margin-bottom:5px;font-weight:300;color:#444}
.bullets li::before{content:"";position:absolute;left:0;top:3px;width:4px;height:4px;background:var(--teal-light)}
.bullets--compact li{font-size:8.2px;line-height:1.32;margin-bottom:3px}
.brand{font-family:"Roboto Condensed",sans-serif;font-weight:300;color:#7a8a96;font-size:19px;position:absolute;right:14px;top:14px;z-index:2}
.photo{position:absolute;left:0;right:0}
/* outside */
.medical{padding:18px 14px 0 16px}
.medical .photo{bottom:0;height:260px;background:linear-gradient(180deg,rgba(255,255,255,0) 0%,rgba(236,228,214,.8) 100%)}
.medical .content{position:relative;z-index:1}
.projects .top{height:272px;padding:18px 12px 0 12px}
.solutions{position:absolute;left:0;right:0;top:272px;bottom:0;background:linear-gradient(180deg,var(--teal-light) 0%,var(--teal) 100%);padding:18px 12px 0;text-align:center}
.solutions p{font-family:"Oswald",sans-serif;color:var(--white);font-size:13.8px;line-height:1.4;text-transform:uppercase}
.contact{list-style:none;text-align:left;margin-top:16px;padding-left:14px}
.contact li{color:var(--white);font-family:"Oswald",sans-serif;font-size:9.5px;display:flex;align-items:center;gap:9px;margin-bottom:4px}
.contact svg{width:11px;height:11px;flex:none}
.cover .photo{top:0;height:272px;background:linear-gradient(160deg,#f6f8fa 0%,#e4ebf0 55%,#cfd9e1 100%)}
.cover-band{position:absolute;left:0;right:0;top:272px;bottom:0;background:linear-gradient(180deg,var(--gold) 0%,var(--gold-deep) 100%);padding:18px 14px 0;text-align:right;color:var(--white)}
.cover-band h1{font-family:"Oswald",sans-serif;font-weight:400;font-size:34px;line-height:1.08;text-transform:uppercase}
.cover-band p{font-family:"Oswald",sans-serif;font-size:8.6px;line-height:1.2;text-transform:uppercase;margin-top:12px}
.cover-band p + p{margin-top:7px}
/* inside */
.why-band{position:absolute;top:0;left:0;width:506.67px;height:80px;background:linear-gradient(180deg,var(--teal-light),#8fd3e6)}
.why-title{position:absolute;top:14px;left:20px;font-family:"Oswald",sans-serif;font-size:40px;line-height:1.2;color:var(--white);font-weight:500;white-space:nowrap}
.body-text{font-size:9.2px;line-height:1.46;font-weight:300;color:#333;margin-bottom:8px}
.why-a{padding:98px 18px 0 20px}
.why-a .lead{font-size:10.6px;margin-top:0}
.why-a .photo{bottom:0;height:240px;background:linear-gradient(180deg,rgba(255,255,255,0) 0%,#cfe3ec 45%,#9fbfd0 100%)}
.why-b{padding:98px 16px 0 14px}
.what{background:linear-gradient(180deg,var(--gold-pale),#fff8e2 60%,#fdeeb8)}
.gold-band{position:absolute;top:0;left:0;right:0;height:80px;background:linear-gradient(180deg,var(--gold),#ffc933)}
.gold-band h2{font-family:"Oswald",sans-serif;color:var(--white);font-weight:500;font-size:18px;line-height:1.12;text-transform:uppercase;position:absolute;left:18px;top:10px}
.what .content{padding:98px 16px 0 18px}
.sub{color:var(--gold-deep);font-weight:700;font-size:10.2px;line-height:1.22;margin-bottom:5px}
.squares{list-style:none}
.squares li{font-size:9.2px;line-height:1.36;font-weight:300;color:#333;padding-left:10px;position:relative;margin-bottom:6px}
.squares li::before{content:"";position:absolute;left:0;top:3px;width:5px;height:5px;background:var(--gold)}
</style>
</head>
<body>

<section class="spread spread--outside">
  <div class="panel medical">
    <div class="photo" role="img" aria-label="Faded photo of medical records on shelves"></div>
    <div class="content">
      <h2 class="heading">MEDICAL OFFICES</h2>
      <p class="lead">Computing resources are much more prevalent, and critical, for supporting profitable Medical Environments.</p>
      <ul class="bullets">
        <li>NorthLoop IT does not have the overhead of a large consulting firm but does have the ability, with our highly experienced staff, to provide whatever services are required to maintain an efficient and economical IT environment that capitalizes on all the productivity features that modern systems now provide.</li>
        <li>NorthLoop IT, based upon the size and requirements of your business, can provide services ranging from evaluating your entire IT environment, making recommendations to tune your existing, or upgrading and enhancing the entire environment.</li>
        <li>We can virtualize your server environment if practical for your requirements. When appropriate, we can even virtualize your desktop environment. This has the potential to not only provide savings at the hardware level but to continually produce savings by also simplifying maintenance and monitoring.</li>
        <li>We can install secure and powerful wireless networks that seamlessly integrate with your wired networks and then both are monitored and controlled from a single access point.</li>
        <li>We have the expertise to know what is appropriate for your best return. Some consulting companies can readily recommend changes, but we always measure returns based on how it improves your bottom line, and what the real costs and ROI are for your specific conditions.</li>
        <li>We can seamlessly integrate your environment, including digitizing your paper records, incorporating scheduling applications. We have integrated an ultrasound machine in one office with the IT environment and enabled image storing as well as remote viewing by authorized remote doctors. We have the expertise to modernize any medical environment.</li>
      </ul>
    </div>
  </div>

  <div class="panel projects">
    <div class="top">
      <h2 class="heading">RECENT PROJECTS</h2>
      <ul class="bullets bullets--compact" style="margin-top:7px">
        <li>Resolved a major problem at Eastbrook University for one of their computer clusters used in their research department.</li>
        <li>Participated in the State of RI twenty million dollar project to upgrade all school environments to provide connectivity for every student on high speed wireless. (1:1 computing)</li>
        <li>Created an open-source implementation in a large commercial environment. Designed an open-source mail server running on the Nimbus cloud for hundreds of users.</li>
        <li>Provided 24x7 monitoring and support for a large boarding school. Implemented an enterprise wireless LAN for a large campus, a campus wide security camera system and a tablet mobile device management system.</li>
        <li>Created a central directory domain and related security for a newly constructed medical office. Connected an ultrasound machine to the IT network and enabled external authorized doctors to securely connect to the server to view ultrasound recordings.</li>
      </ul>
    </div>
    <div class="solutions">
      <p>Our solutions for schools, medical/dental, small businesses and auto dealerships are cost effective because they are customized specifically for your environment. Your type of business and end users are critical factors that should be the influencing design parameters</p>
      <ul class="contact">
        <li><svg viewBox="0 0 12 12"><circle cx="6" cy="6" r="5.3" fill="none" stroke="#fff" stroke-width="1.2"/><rect x="3" y="4" width="6" height="4" fill="#fff"/></svg>www.northloopit.com</li>
        <li><svg viewBox="0 0 12 12"><circle cx="6" cy="6" r="5.3" fill="none" stroke="#fff" stroke-width="1.2"/><path d="M3 4h6v4H3z M3 4l3 2.2L9 4" fill="none" stroke="#fff" stroke-width=".9"/></svg>info@northloopit.com</li>
        <li><svg viewBox="0 0 12 12"><circle cx="6" cy="6" r="5.3" fill="none" stroke="#fff" stroke-width="1.2"/><path d="M4 3.2c-.8.8-.6 2.6 1.2 4.4s3.5 2 4.3 1.2l-1.2-1.3-1 .5-2-2 .5-1z" fill="#fff"/></svg>401-555-0142</li>
        <li><svg viewBox="0 0 12 12"><circle cx="6" cy="6" r="5.3" fill="none" stroke="#fff" stroke-width="1.2"/><path d="M6 2.6a2.2 2.2 0 0 1 2.2 2.2C8.2 6.5 6 9.3 6 9.3S3.8 6.5 3.8 4.8A2.2 2.2 0 0 1 6 2.6z" fill="#fff"/><circle cx="6" cy="4.8" r=".8" fill="#1f9fc4"/></svg>18 Elm St #210 Harborview, RI 02900</li>
      </ul>
    </div>
  </div>

  <div class="panel cover">
    <div class="brand">NorthLoop IT</div>
    <div class="photo" role="img" aria-label="Photo of two doctors in white coats"></div>
    <div class="cover-band">
      <h1>Design,<br>Installation &amp;<br>Management<br>of Computing<br>Environments</h1>
      <p>We can monitor(24x7), design,<br>install or modify</p>
      <p>IT environments customized for schools,<br>medical/dental, small businesses and auto<br>dealerships</p>
      <p>Security camera monitoring systems<br>economically integrated into the IT<br>environment</p>
    </div>
  </div>
</section>

<section class="spread spread--inside">
  <div class="why-band"><div class="why-title">WHY OUTSOURCE?</div></div>

  <div class="panel why-a">
    <div class="photo" role="img" aria-label="Photo of a doctor's hands using a tablet at a desk"></div>
    <div style="position:relative;z-index:1">
      <p class="lead">We specialized in IT support at a scale tailored to your exact requirements</p>
      <p class="body-text">A direct, dedicated IT staff will have either idle time during periods of stability or inadequate resources for those times when problems occur simultaneously.</p>
      <p class="body-text">By outsourcing to NorthLoop IT your business will always have the ideal level of support, and therefore never overpay nor be insufficiently prepared to deal with sudden problems that can overwhelm insufficient numbers of staff.</p>
      <p class="body-text">Because funds are allocated efficiently your business can now afford to capitalize on the most current technology and benefit from all features offered by these newest features.</p>
    </div>
  </div>

  <div class="panel why-b">
    <p class="body-text">Outsourcing is the better economical choice; there are no overtime hours, paid vacations, morale problems, costs associated with health care and mandatory reporting, and other overhead expenses associated with employees.</p>
    <p class="body-text">But cost is not the only reason to outsource. Your core business is not IT; therefore outsourcing eliminates the need for your personnel to be proficient in multiple areas, i.e. building specialized skills to support your core businesses and functions as well as accumulating skills enabling them to manage, enhance and maintain the ideal IT environment.</p>
    <p class="body-text">The elimination of this responsibility allows you to focus on finding and developing personnel skills directly related to your business, and not compromising your core business components.</p>
  </div>

  <div class="panel what">
    <div class="gold-band"><h2>What we do<br>for all types of IT<br>environments</h2></div>
    <div class="content">
      <p class="sub">Install, customize and support all elements of IT environments</p>
      <p class="body-text">We analyze your unique business requirements, determining if modifications are cost justified for your existing computing environment.</p>
      <p class="sub">Design the best combination of hardware and software for your environment</p>
      <p class="body-text">We specialize in Windward, Netrix, open-source, Orchard, tablets and smart phones. We are able to structure each solution to the specific type of business to achieve the best returns on investment.</p>
      <p class="sub">Tailor all components of the entire IT environment</p>
      <p class="body-text" style="margin-bottom:6px">Install, customize, monitor</p>
      <ul class="squares">
        <li>desktops</li>
        <li>multiple operating systems (Windward, Orchard, open-source)</li>
        <li>Tablets</li>
        <li>network backbones and their components (Ethernet, fiber, routers, switches, advanced wireless)</li>
        <li>servers</li>
        <li>virtualization (thin clients/zero clients)</li>
        <li>firewalls</li>
        <li>virus/intruder detection</li>
        <li>data encryption</li>
        <li>data analysis and more</li>
      </ul>
    </div>
  </div>
</section>

</body>
</html>
```